Computer consultant business card

Bexil Software is a newly started computer consulting company. It's a small one-man company that provides mostly Vornix applications but also websites in collaboration with designers. I'm running this company on the side of full time university studies.

I want the final design to be clean and memorable. Be creative! :)

Some inspiration:
http://www.pixelmarta.com/design/48317
http://www.pixelmarta.com/design/2739164/business-card-design-by-frostlynk
http://www.pixelmarta.com/design/604281/business-card-design-by-koralind-vestrabanu

See attachment for my company logo.
Updates

I would like to thank everyone for submitting! I'll need a couple of days to review and ultimately select a design.

Target Market(s)

Non-technical entrepreneurs and small companies.

Industry/Entity Type

University

Requirements
Must have
• My company logo.
In any way, both colors from my logo.
First- and last name, e-mail and phone number.
Double-sided design.
Nice to have
• Something creative with the symbol in my logo

```html
<!DOCTYPE html>
<html lang="en">
<head>
<meta charset="utf-8">
<title>Vimtrel – Business Card</title>
<link rel="stylesheet" href="https://fonts.googleapis.com/css2?family=Exo+2:wght@300;400;500&display=swap">
<style>
  :root {
    --brand-blue: #4a7ccb;
    --brand-grey: #3b3b3d;
    --brand-grey-dark-card: #464648;
    --ink-soft: #55565a;
    --card-light-top: #f4f4f5;
    --card-light-bottom: #d9dadc;
    --card-dark: #0d0d0e;
    --pattern-dark: #1e1e20;
    --pattern-mid: #2c2c2e;
    --backdrop: #262627;
  }
  * { box-sizing: border-box; margin: 0; padding: 0; }
  html, body {
    width: 1200px;
    height: 900px;
    overflow: hidden;
    background: var(--backdrop);
    font-family: "Exo 2", sans-serif;
  }
  .canvas {
    position: relative;
    width: 1200px;
    height: 900px;
  }
  .card {
    position: absolute;
    left: 320px;
    width: 560px;
    height: 320px;
    overflow: hidden;
  }

  /* Front side */
  .card--front {
    top: 90px;
    background: linear-gradient(160deg, var(--card-light-top) 0%, #e9e9ea 55%, var(--card-light-bottom) 100%);
  }
  .brand {
    position: absolute;
    display: flex;
    align-items: center;
    color: var(--brand-grey);
    font-weight: 500;
    letter-spacing: 0.01em;
    white-space: nowrap;
  }
  .brand__dot {
    border-radius: 50%;
    background: var(--brand-blue);
    flex: none;
  }
  .card--front .brand {
    left: 48px;
    top: 170px;
    font-size: 44px;
    gap: 12px;
  }
  .card--front .brand__dot { width: 44px; height: 44px; }
  .divider {
    position: absolute;
    left: 300px;
    top: 78px;
    width: 1px;
    height: 150px;
    background: var(--brand-blue);
  }
  .contact {
    position: absolute;
    left: 322px;
    top: 78px;
    color: var(--ink-soft);
  }
  .contact__name {
    color: var(--brand-blue);
    font-size: 26px;
    font-weight: 400;
    letter-spacing: 0.06em;
    line-height: 1;
  }
  .contact__role {
    margin-top: 6px;
    font-size: 14px;
    font-weight: 400;
  }
  .contact__list {
    list-style: none;
    margin-top: 22px;
    font-size: 14px;
    font-weight: 300;
  }
  .contact__list li {
    display: flex;
    align-items: center;
    gap: 9px;
    margin-bottom: 6px;
  }
  .contact__icon { width: 13px; height: 13px; flex: none; }

  /* Back side */
  .card--back {
    top: 470px;
    background: var(--card-dark);
  }
  .pattern {
    position: absolute;
    inset: 0;
    background:
      linear-gradient(112deg, transparent 0 22%, rgba(0,0,0,0.55) 22% 28%, transparent 28%),
      linear-gradient(180deg, var(--pattern-mid) 0%, var(--pattern-dark) 55%, var(--card-dark) 100%);
  }
  .card--back .brand {
    left: 170px;
    top: 112px;
    font-size: 70px;
    gap: 18px;
    color: var(--brand-grey-dark-card);
  }
  .card--back .brand__dot { width: 84px; height: 84px; }
  .web {
    position: absolute;
    left: 274px;
    top: 212px;
    color: var(--brand-blue);
    font-size: 19px;
    font-weight: 400;
    letter-spacing: 0.2em;
    white-space: nowrap;
  }
</style>
</head>
<body>
<main class="canvas">

  <section class="card card--front" aria-label="Business card front">
    <div class="brand">
      <span class="brand__dot"></span>
      <span class="brand__name">vimtrel</span>
    </div>

    <div class="divider"></div>

    <div class="contact">
      <h1 class="contact__name">MARTEN VALE</h1>
      <p class="contact__role">Managing Director</p>
      <ul class="contact__list">
        <li>
          <svg class="contact__icon" viewBox="0 0 16 16" aria-hidden="true">
            <rect x="3" y="1" width="10" height="14" rx="2" fill="var(--brand-blue)"/>
            <rect x="5" y="3" width="6" height="8" fill="#fff"/>
            <circle cx="8" cy="13" r="0.9" fill="#fff"/>
          </svg>
          <span>+ (00) 1 47 382 9160</span>
        </li>
        <li>
          <svg class="contact__icon" viewBox="0 0 16 16" aria-hidden="true">
            <rect x="1" y="3" width="14" height="10" rx="1" fill="var(--brand-blue)"/>
            <path d="M1.5 3.8 8 9 14.5 3.8" fill="none" stroke="#fff" stroke-width="1.2"/>
          </svg>
          <span>marten@vimtrel.com.au</span>
        </li>
      </ul>
    </div>
  </section>

  <section class="card card--back" aria-label="Business card back">
    <div class="pattern" role="img" aria-label="Repeating pattern of the brand symbol in dark grey tones"></div>
    <div class="brand">
      <span class="brand__dot"></span>
      <span class="brand__name">vimtrel</span>
    </div>
    <p class="web">www.vimtrel.com.au</p>
  </section>

</main>
</body>
</html>
```